Brivolt Technologies business card design

We need a business card designed with our new logo. it would be great if the card could communicate it is a technology based company.

Target Market(s)

system integrators

Industry/Entity Type

technology, IOT

Contact Information for Business Card

Name, designation, Address, telephone number, email address

Requirements
Must have
• logo and company name
Nice to have
• something to do with technology

```html
<!DOCTYPE html>
<html lang="en">
<head>
<meta charset="utf-8">
<title>Brivolt Technologies – Business Card</title>
<link rel="stylesheet" href="https://fonts.googleapis.com/css2?family=Open+Sans:wght@400;600;700&display=swap">
<style>
  :root {
    --backdrop: #1c1c1e;
    --card-dark: #3c3c3e;
    --card-light: #ffffff;
    --ink: #2a2a2c;
    --brand-orange: #f39325;
    --band-grey: #3c3c3e;
    --text-on-dark: #ffffff;
  }
  * { margin: 0; padding: 0; box-sizing: border-box; }
  html, body {
    width: 1200px; height: 864px; overflow: hidden;
    background: var(--backdrop);
    font-family: "Open Sans", Arial, sans-serif;
  }
  .canvas {
    position: relative; width: 1200px; height: 864px;
    display: flex; flex-direction: column; align-items: center; justify-content: center; gap: 48px;
  }
  .card {
    position: relative; width: 560px; height: 320px;
    border-radius: 18px; overflow: hidden;
    box-shadow: 0 18px 40px rgba(0,0,0,0.45);
  }
  .card--front { background: var(--card-dark); display: flex; align-items: center; justify-content: center; }
  .card--back { background: var(--card-light); }

  .wordmark { display: flex; align-items: center; gap: 12px; white-space: nowrap; }
  .wordmark__square { width: 26px; height: 26px; background: var(--brand-orange); flex: none; }
  .wordmark__name { font-weight: 700; letter-spacing: 1px; text-transform: uppercase; }
  .card--front .wordmark__name { color: var(--text-on-dark); font-size: 34px; }
  .card--back .wordmark { position: absolute; left: 30px; top: 200px; gap: 10px; }
  .card--back .wordmark__square { width: 16px; height: 16px; }
  .card--back .wordmark__name { color: var(--ink); font-size: 17px; letter-spacing: 0.5px; }

  .divider {
    position: absolute; left: 318px; top: 44px; width: 2px; height: 176px;
    background: var(--brand-orange);
  }
  .contact { position: absolute; left: 338px; top: 48px; color: var(--ink); }
  .contact__name { color: var(--brand-orange); font-weight: 700; font-size: 20px; text-transform: uppercase; line-height: 1.1; }
  .contact__title { font-size: 14px; margin-top: 4px; }
  .contact__address { font-size: 14px; line-height: 1.35; margin-top: 14px; }
  .contact__line { display: flex; align-items: center; gap: 8px; font-size: 14px; margin-top: 6px; }
  .contact__line:first-of-type { margin-top: 12px; }
  .contact__icon { width: 14px; height: 14px; flex: none; }

  .footer-bands { position: absolute; left: 0; top: 0; width: 560px; height: 320px; }
  .web-address {
    position: absolute; right: 20px; bottom: 15px;
    color: var(--text-on-dark); font-size: 15px; font-weight: 600;
  }
</style>
</head>
<body>
<main class="canvas">
  <section class="card card--front" aria-label="Card front">
    <div class="wordmark">
      <span class="wordmark__square"></span>
      <span class="wordmark__name">Brivolt Technologies</span>
    </div>
  </section>

  <section class="card card--back" aria-label="Card back">
    <svg class="footer-bands" viewBox="0 0 560 320" aria-hidden="true">
      <polygon points="0,296 290,296 312,264 318,264 294,300 0,300" fill="var(--brand-orange)"/>
      <polygon points="0,305 297,305 320,272 336,272 336,320 0,320" fill="var(--band-grey)"/>
      <polygon points="344,262 560,262 560,320 306,320" fill="var(--brand-orange)"/>
    </svg>

    <div class="wordmark">
      <span class="wordmark__square"></span>
      <span class="wordmark__name">Brivolt Technologies</span>
    </div>

    <div class="divider"></div>

    <div class="contact">
      <p class="contact__name">Tavin Rourke</p>
      <p class="contact__title">Owner/Co-Founder</p>
      <p class="contact__address">Lumen Court 2100 Park<br>Harlow WD Suite 118</p>
      <p class="contact__line">
        <svg class="contact__icon" viewBox="0 0 24 24" aria-hidden="true"><path fill="var(--brand-orange)" d="M6.6 10.8c1.4 2.8 3.8 5.1 6.6 6.6l2.2-2.2c.3-.3.7-.4 1-.2 1.1.4 2.3.6 3.6.6.6 0 1 .4 1 1V20c0 .6-.4 1-1 1C10.6 21 3 13.4 3 4c0-.6.4-1 1-1h3.5c.6 0 1 .4 1 1 0 1.3.2 2.5.6 3.6.1.3 0 .7-.2 1z"/></svg>
        555-014-2730
      </p>
      <p class="contact__line">
        <svg class="contact__icon" viewBox="0 0 24 24" aria-hidden="true"><path fill="var(--brand-orange)" d="M2 5h20v14H2z"/><path fill="none" stroke="#fff" stroke-width="1.8" d="M2.5 5.8 12 13l9.5-7.2"/></svg>
        info@brivolttech.com
      </p>
    </div>

    <p class="web-address">www.brivolttech.com</p>
  </section>
</main>
</body>
</html>
```